Graphic Design Zephyrmart Book Description

There is a book on Zephyrmart that is my competitor that has a large graphic design as part of the description for the book and I want a similar thing for my book to make it stand out more.

My competitors book is here: https://www.zephyrmart.example/Stellar-Chemistry-Novices-Grasping-Walkthrough/dp/K47RTPW612/

My book is here: https://www.zephyrmart.example/Stellar-Chemistry-Groundwork-Reactions-Bonding/dp/K9HXCVT27S/

You can see the kind of thing I am looking for on the book listing but I have attached an image below.

Thanks

Trevor

```html
<!DOCTYPE html>
<html lang="en">
<head>
<meta charset="utf-8">
<title>Quantum Physics – Book Description Graphic</title>
<link href="https://fonts.googleapis.com/css2?family=Oswald:wght@300;400;500;600;700&family=Poppins:wght@300;400;600;700&display=swap" rel="stylesheet">
<style>
:root{
  --navy:#1d2150;
  --navy-deep:#0f1233;
  --yellow:#ece12a;
  --book-yellow:#e3da2a;
  --page:#f2eee6;
  --red:#d4141f;
  --red-dark:#8e0a12;
  --white:#ffffff;
  --ink:#1a1a1a;
  --divider:#6b6b6b;
}
*{margin:0;padding:0;box-sizing:border-box}
html,body{width:852px;height:1200px;overflow:hidden;background:var(--white)}
.poster{position:relative;width:852px;height:1200px;background:var(--white);font-family:"Poppins",sans-serif;color:var(--ink);overflow:hidden}

/* hero */
.hero{position:absolute;left:0;top:0;width:852px;height:469px;
  background:radial-gradient(ellipse 460px 170px at 250px 480px,#7aa0d4 0%,#2f4384 45%,transparent 75%),
             radial-gradient(circle 110px at 300px 350px,#ffb35a 0%,#d0542d 45%,transparent 100%),
             linear-gradient(180deg,#1b1e4d 0%,#262c63 55%,#141840 100%)}
.rule{position:absolute;background:var(--yellow)}
.rule-top{left:374px;top:0;width:4px;height:66px}
.rule-side{left:74px;top:226px;width:4px;height:243px}

.kicker{position:absolute;left:74px;top:82px;font-weight:600;font-size:29px;line-height:1.2;letter-spacing:11px;color:var(--white);white-space:nowrap}
.headline{position:absolute;left:74px;font-family:"Oswald",sans-serif;font-weight:600;color:var(--yellow);font-size:48px;line-height:1;letter-spacing:-.5px;white-space:nowrap}
.headline.l1{top:120px}
.headline.l2{top:175px}
.subject{position:absolute;left:88px;font-weight:600;color:var(--white);font-size:54px;line-height:1;white-space:nowrap}
.subject.l1{top:226px}
.subject.l2{top:273px}

/* product shots */
.book-page{position:absolute;left:412px;top:248px;width:200px;height:92px;background:var(--book-yellow);transform:rotate(-10deg);box-shadow:0 4px 10px rgba(0,0,0,.35);z-index:1}
.book-cover{position:absolute;left:612px;top:205px;width:185px;height:285px;background:var(--book-yellow);transform:rotate(14deg);box-shadow:0 6px 14px rgba(0,0,0,.4);z-index:1}
.book-spread{position:absolute;left:372px;top:318px;width:320px;height:191px;background:linear-gradient(90deg,var(--page) 0%,#e4ded2 49%,#cfc8ba 50%,var(--page) 52%,#e8e3d9 100%);box-shadow:0 6px 14px rgba(0,0,0,.35);z-index:2}

/* seals */
.seal{position:absolute;border-radius:50%;display:flex;flex-direction:column;align-items:center;justify-content:center;text-align:center;background:var(--red);box-shadow:0 0 0 7px var(--red-dark),0 4px 14px 7px rgba(0,0,0,.35);z-index:3}
.seal-gift{left:585px;top:45px;width:186px;height:186px}
.seal-gift .top{font-family:"Oswald",sans-serif;font-weight:500;color:var(--white);font-size:21px;line-height:1.05}
.seal-gift .mid{font-family:"Oswald",sans-serif;font-weight:300;color:var(--white);font-size:16px;line-height:1.2;letter-spacing:1px}
.seal-gift .hl{font-weight:700;color:var(--yellow);font-size:21px;line-height:1.05}
.seal-ideal{left:287px;top:364px;width:152px;height:152px;z-index:4}
.seal-ideal .top{color:var(--white);font-size:11px;letter-spacing:2.5px;line-height:1.4}
.seal-ideal .hl{font-family:"Oswald",sans-serif;font-weight:500;color:var(--yellow);font-size:13.5px;line-height:1.3;white-space:nowrap}
.seal-ideal .stars{color:var(--white);font-size:14px;letter-spacing:2px;margin-top:3px}

/* feature columns */
.features{position:absolute;left:56px;top:529px;display:flex}
.feature{text-align:center;border-right:1.5px dashed var(--divider);display:flex;flex-direction:column;align-items:center}
.feature:last-child{border-right:none}
.feature.c1{width:172px}
.feature.c2{width:195px}
.feature.c3{width:174px}
.feature.c4{width:195px}
.feature h3{font-weight:400;font-size:15px;line-height:1.17;text-transform:uppercase;height:53px;display:flex;flex-direction:column;justify-content:center;white-space:nowrap}
.feature h3 b{font-weight:700}
.feature .dash{width:13px;height:2px;background:var(--ink);margin:5px auto 10px}
.feature p{font-weight:300;font-size:14px;line-height:16.5px;white-space:nowrap}

/* contents */
.contents{position:absolute;left:46px;top:766px;width:752px;height:434px;border-radius:22px 22px 0 0;
  background:radial-gradient(ellipse 300px 120px at 420px 150px,#3a3f86 0%,transparent 80%),linear-gradient(180deg,var(--navy) 0%,var(--navy-deep) 100%)}
.stack{position:absolute;left:0;top:750px;width:370px;height:380px;z-index:2}
.stack-lying{position:absolute;inset:0;background:var(--book-yellow);clip-path:polygon(0 276px,262px 286px,362px 320px,362px 347px,215px 375px,0 314px)}
.stack-standing{position:absolute;left:65px;top:2px;width:218px;height:305px;background:var(--book-yellow);box-shadow:6px 6px 14px rgba(0,0,0,.35)}

.contents-title{position:absolute;left:392px;top:789px;font-family:"Oswald",sans-serif;font-size:32px;line-height:1;color:var(--white);font-weight:300;letter-spacing:-1px;white-space:nowrap}
.contents-title b{font-weight:700}
.chapters{position:absolute;left:390px;top:838px;width:344px;list-style:none}
.chapter{position:absolute;left:0;width:100%;border-radius:6px;background:var(--white);font-weight:600;font-size:13.5px;line-height:15.7px;padding:0 8px;display:flex;align-items:center;white-space:nowrap;letter-spacing:-.1px}
.chapter.alt{background:var(--yellow)}
</style>
</head>
<body>
<main class="poster">
  <section class="hero" role="img" aria-label="Deep space background with a glowing sunrise over a blue planet horizon and faint atom orbit lines"></section>
  <div class="rule rule-top"></div>
  <div class="rule rule-side"></div>

  <p class="kicker">EMBARK ON A</p>
  <h1 class="headline l1">MIND-BENDING JOURNEY</h1>
  <p class="headline l2">INTO THE REALM OF</p>
  <p class="subject l1">QUANTUM</p>
  <p class="subject l2">PHYSICS</p>

  <div class="book-page" role="img" aria-label="Yellow back cover page with the book blurb"></div>
  <div class="book-cover" role="img" aria-label="Yellow book cover titled Quantum Physics"></div>
  <div class="book-spread" role="img" aria-label="Open book showing the introduction and first chapter pages"></div>

  <div class="seal seal-gift">
    <span class="top">PERFECT GIFT</span>
    <span class="mid">FOR THE</span>
    <span class="hl">SCIENCE<br>LOVER</span>
  </div>
  <div class="seal seal-ideal">
    <span class="top">IDEAL FOR</span>
    <span class="hl">SCIENCE STUDENTS,<br>QUANTUM COMPUTING<br>ENTHUSIASTS</span>
    <span class="stars">★★★</span>
  </div>

  <section class="features">
    <article class="feature c1">
      <h3><span>History of</span><b>Quantum</b><b>Mechanics</b></h3>
      <div class="dash"></div>
      <p>Explore the<br>fascinating history<br>of quantum<br>mechanics and<br>the brilliant minds<br>behind its<br>development</p>
    </article>
    <article class="feature c2">
      <h3><span>Fundamental</span><span>principles of</span><b>Wave-Particle</b></h3>
      <div class="dash"></div>
      <p>Grasp the<br>fundamental<br>principles of wave-<br>particle duality,<br>quantum states, and<br>the uncertainty<br>principle</p>
    </article>
    <article class="feature c3">
      <h3><b>Quantum</b><b>Entanglement</b></h3>
      <div class="dash"></div>
      <p>Dive into the<br>strange and<br>counterintuitive<br>world of quantum<br>entanglement and<br>its implications for<br>reality itself</p>
    </article>
    <article class="feature c4">
      <h3><span>Quantum</span><span>computing to</span><b>Cryptography</b></h3>
      <div class="dash"></div>
      <p>Learn about the<br>cutting- edge<br>applications of<br>quantum mechanics,<br>from quantum<br>computing to<br>cryptography</p>
    </article>
  </section>

  <section class="contents" role="img" aria-label="Starry galaxy background"></section>
  <div class="stack" role="img" aria-label="Stack of yellow Quantum Physics paperback books by Elias Warden">
    <div class="stack-lying"></div>
    <div class="stack-standing"></div>
  </div>

  <h2 class="contents-title">IN THIS BOOK <b>YOU WILL FIND</b></h2>
  <ul class="chapters">
    <li class="chapter alt" style="top:0;height:23px">The Quantum World Unveiled</li>
    <li class="chapter" style="top:30px;height:38px">The Mathematical Symphony of<br>Quantum Mechanics</li>
    <li class="chapter alt" style="top:76px;height:24px">Beyond Classical Boundaries</li>
    <li class="chapter" style="top:106px;height:24px">Quantum Mechanics at Work</li>
    <li class="chapter alt" style="top:137px;height:25px">Bridging Quantum Mechanics &amp; Relativity</li>
    <li class="chapter" style="top:169px;height:38px">Quantum Paradoxes and Thought<br>Experiments</li>
    <li class="chapter alt" style="top:216px;height:23px">Quantum Mechanics for the Curious Mind</li>
    <li class="chapter" style="top:248px;height:37px">Quantum Mechanics Demystified -<br>A Practical Guide</li>
  </ul>
</main>
</body>
</html>
```